I have a tallow based business and I want to streamline my products

I have roughly 10 items that I would like to make lebals for in order to streamline my business, I am attaching the current design and am willing to work with this but would also like to see if you come up with something different, my biggest seller is my facewash , my webpage is meadowhearthco,com my current designs are below- The newest one is the light brown version which I do like but I am not sure how that will integrate or be streamlined with the remaining products, If you believe it can look similar and still be attractive, I am ok with that too,

My current Label Project Needs:

Tallow + Magnesium Lotion biodegradable wheat bottle
Tallow Cream Face Wash - biodegradable what bottle
Tallow Body Butter 8 oz jar with bamboo lid
Tallow Deodorant will be printed on a Kraft Paper tube
Tallow Face Cream for Day wear 2 oz glass jar with bamboo lid
Vitamin C Serum 2 oz serum bottle with bamboo pump
Blue Algae Toner 4 oz glass bottle
Tallow + Hyaluronic 2oz face cream jar
'
My project is to display sustainable products, eco friendly packaging, organic , natural and holistic

I am ok with the newest label I attached but I am also ok with a minimalistic project, I would love to choose from a couple of designs.

Thank you so much

```html
<!DOCTYPE html>
<html lang="en">
<head>
<meta charset="utf-8">
<title>Meadow Hearth Organics – Face Cream Label</title>
<link href="https://fonts.googleapis.com/css2?family=Marcellus&family=Jost:wght@400;500;600&family=Noto+Serif:wght@400;700&display=swap" rel="stylesheet">
<style>
  :root {
    --page: #efefef;
    --label: #f1e9dc;
    --front: #f4efe5;
    --ink: #4a3b3a;
    --ink-soft: #6b5d5b;
    --rule: #cfc4b4;
    --pill-text: #f1e9dc;
  }
  html, body {
    margin: 0; padding: 0;
    width: 1200px; height: 1200px;
    overflow: hidden;
    background: var(--page);
  }
  .label {
    position: absolute;
    left: 40px; top: 271px;
    width: 1120px; height: 658px;
    background: var(--label);
    color: var(--ink);
  }
  /* ---------- left panel ---------- */
  .claims { position: absolute; left: 0; top: 0; width: 363px; height: 100%; }
  .claim {
    position: absolute; left: 80px; width: 260px;
    display: flex; align-items: center; gap: 26px;
    font-family: "Jost", sans-serif; font-weight: 500;
    font-size: 15px; line-height: 1.15; letter-spacing: 0.2px;
    text-transform: uppercase;
  }
  .claim-icon {
    width: 50px; height: 50px; border-radius: 50%;
    background: #d9cdbb; flex: none;
  }
  .claim-rule {
    position: absolute; left: 57px; width: 267px; height: 1px;
    background: var(--rule);
  }
  .maker {
    position: absolute; left: 57px; top: 522px;
    width: 264px; height: 88px;
    border: 1.5px solid var(--ink); border-radius: 5px;
    box-sizing: border-box;
    display: flex; flex-direction: column; justify-content: center; align-items: center;
    font-family: "Jost", sans-serif; font-size: 11px; line-height: 1.6;
    text-transform: uppercase; text-align: center;
  }
  .maker strong { font-weight: 600; }
  .maker .web { text-transform: none; }
  /* ---------- front panel ---------- */
  .front {
    position: absolute; left: 363px; top: 0;
    width: 469px; height: 100%;
    background: var(--front);
    text-align: center;
  }
  .brand {
    position: absolute; top: 84px; left: 0; right: 0;
    font-family: "Jost", sans-serif; font-size: 18px; letter-spacing: 1.6px;
    text-transform: uppercase; color: var(--ink-soft);
  }
  .title {
    position: absolute; top: 118px; left: 0; right: 0;
    margin: 0;
    font-family: "Marcellus", serif; font-weight: 400;
    font-size: 108px; line-height: 94px; letter-spacing: 1px;
    color: var(--ink);
  }
  .title .l2 { font-size: 114px; }
  .variant {
    position: absolute; top: 344px; left: 115px;
    width: 238px; height: 34px;
    background: var(--ink); border-radius: 4px 10px 4px 10px;
    font-family: "Jost", sans-serif; font-size: 19px; line-height: 34px;
    letter-spacing: 0.8px; color: var(--pill-text); text-transform: uppercase;
  }
  .emblem {
    position: absolute; top: 416px; left: 155px;
    width: 150px; height: 96px; border-radius: 8px;
    background: #5a4443;
  }
  .benefits {
    position: absolute; top: 548px; left: 0; right: 0;
    font-family: "Jost", sans-serif; font-weight: 500; font-size: 27px;
    color: var(--ink);
  }
  .netwt {
    position: absolute; top: 598px; left: 0; right: 0;
    font-family: "Jost", sans-serif; font-size: 14px; color: var(--ink-soft);
  }
  /* ---------- right panel ---------- */
  .ingredients {
    position: absolute; left: 870px; top: 84px;
    height: 530px;
    display: flex; gap: 14px;
    writing-mode: vertical-rl; transform: rotate(180deg);
  }
  .ingredients h2 {
    margin: 0; padding: 6px 4px;
    height: 290px; box-sizing: border-box;
    background: var(--ink); color: var(--label);
    font-family: "Noto Serif", serif; font-weight: 700; font-size: 17px;
    text-align: center; line-height: 22px;
  }
  .ingredients p {
    margin: 0; width: 160px;
    font-family: "Noto Serif", serif; font-size: 14.2px; line-height: 21px;
    letter-spacing: 0.6px; text-align: justify; color: var(--ink);
  }
</style>
</head>
<body>
  <main class="label">
    <section class="claims">
      <div class="claim" style="top:100px">
        <svg class="claim-icon" role="img" aria-label="Cow head icon" viewBox="0 0 50 50"></svg>
        <span>Grass fed<br>tallow</span>
      </div>
      <div class="claim-rule" style="top:184px"></div>
      <div class="claim" style="top:216px">
        <svg class="claim-icon" role="img" aria-label="Leaf in circle icon" viewBox="0 0 50 50"></svg>
        <span>Organic<br>ingredients</span>
      </div>
      <div class="claim-rule" style="top:293px"></div>
      <div class="claim" style="top:322px">
        <svg class="claim-icon" role="img" aria-label="Hand with heart icon" viewBox="0 0 50 50"></svg>
        <span>Hand crafted</span>
      </div>
      <div class="claim-rule" style="top:401px"></div>
      <div class="claim" style="top:433px">
        <svg class="claim-icon" role="img" aria-label="Handshake icon" viewBox="0 0 50 50"></svg>
        <span>Fair trade</span>
      </div>
      <div class="maker">
        <span>Manufactured by</span>
        <strong>Meadow Hearth Organics</strong>
        <span>PO. Box : 4417 Fairhaven, VA 23410</span>
        <span class="web">meadowhearthco.com</span>
      </div>
    </section>

    <section class="front">
      <div class="brand">Meadow Hearth Organics</div>
      <h1 class="title">FACE<br><span class="l2">CREAM</span></h1>
      <div class="variant">Tallow Cream</div>
      <svg class="emblem" role="img" aria-label="Cow silhouette illustration" viewBox="0 0 150 96"></svg>
      <div class="benefits">Cleanse • Purify • Moisturize</div>
      <div class="netwt">NET WT. 8 OZ (236ML)</div>
    </section>

    <section class="ingredients">
      <h2>Our Amazing Ingredients:</h2>
      <p>Distilled Water, Lavender Hydrosol, Glycerin, Grass Fed Tallow, Daucus Carota (Carrot Seed Oil), Oenothera Biennis (Rosehip Oil), Simmondsia Chinensis (Jojoba Oil) Cocos Nucifera (Coconut Oil), Cucurbita Pepo Seed Oil (Pumpkin Seed Oil) Coenzyme Q10 (CoQ10) Niacinamide, Vitamin B3 Citrus Paradisi Seed Oil (Grapefruit Seed oil), Decyl Glucoside, Cetyl Alcohol Citric Acid, Xanthan Gum, Sodium Benzoate (Preservative)</p>
    </section>
  </main>
</body>
</html>
```